Website Design for Employee Moral and Happiness Company

Looking for a clean website design that explains our features in a step by step manner so our visitors know exactly what our site does before logging in.

The site is called "Velrato". See logo design and video for a sample of style and an overview of what we do.

Target Market(s)

Business owners that are looking to retain employees.

Number of Pages Required

1 page

```html
<!DOCTYPE html>
<html lang="en">
<head>
<meta charset="utf-8">
<title>Velrato — Employee Morale and Happiness</title>
<link href="https://fonts.googleapis.com/css2?family=Lora:wght@400;500;600;700&display=swap" rel="stylesheet">
<style>
:root{
  --orange:#fc5108;
  --blue:#4a8af4;
  --ink:#111111;
  --text:#5a5a5a;
  --peach:#fbeae1;
  --footer:#1d1d1f;
  --white:#ffffff;
}
*{margin:0;padding:0;box-sizing:border-box}
html,body{width:1200px;height:3382px;overflow:hidden;background:var(--white)}
body{position:relative;font-family:"Lora",Georgia,serif;color:var(--ink)}
.abs{position:absolute}
a{color:inherit;text-decoration:none}

/* header */
.brand{left:144px;top:8px;font-size:60px;font-weight:700;color:var(--ink);letter-spacing:1px}
.nav{left:521px;top:36px;font-size:17px;font-weight:500}
.nav a{position:absolute;white-space:nowrap}
.nav .active::after{content:"";position:absolute;left:50%;top:26px;width:14px;height:6px;margin-left:-7px;border-bottom:3px solid var(--orange);border-radius:0 0 10px 10px}
.btn{display:flex;align-items:center;justify-content:center;border-radius:24px;color:var(--white);font-size:14px;font-weight:700;letter-spacing:.3px}
.btn-orange{background:var(--orange)}
.btn-blue{background:var(--blue)}
.login{left:962px;top:26px;width:95px;height:42px}

/* hero */
.hero-media{left:43px;top:101px;width:1112px;height:575px;background:linear-gradient(135deg,#e1d7ce 0%,#e1d7ce 8%,#1f3c66 22%,#2fa8a4 45%,#e0d6cc 70%,#e0d6cc 100%)}
.play{left:561px;top:349px;width:80px;height:80px}
.hero-title{left:0;top:748px;width:1200px;text-align:center;font-size:62px;font-weight:700;color:var(--white)}
.hero-copy{left:249px;top:848px;width:702px;text-align:center;font-size:16.5px;line-height:30.3px;color:var(--white)}
.hero-more{left:524px;top:1037px;width:153px;height:45px}

/* features */
.section-title{left:0;width:1200px;text-align:center;font-size:64px;font-weight:700}
.feature{width:300px;text-align:center}
.feature-icon{width:190px;height:190px;margin:0 auto;border-radius:50%}
.feature h3{margin-top:20px;font-size:25px;font-weight:600;line-height:32px}
.feature p{width:270px;margin:12px auto 0;font-size:14.5px;line-height:25.5px;color:var(--text)}
.feature .btn{width:154px;height:44px;margin:30px auto 0}

.peach{left:0;top:1969px;width:1200px;height:778px;border-radius:50%;background:var(--peach)}

.card{width:277px;height:353px;background:var(--white);border:2px solid #cfcfcf}
.card.raised{box-shadow:0 4px 14px rgba(0,0,0,.25)}
.card-art{position:absolute;left:14px;top:8px;width:245px;height:160px;border-radius:6px;background:linear-gradient(135deg,#e9e6f3,#c9d3ee 55%,#f0dcd2)}
.date{position:absolute;left:19px;top:187px;width:46px;height:46px;background:var(--blue);color:var(--white);text-align:center;font-size:20px;line-height:22px;padding-top:3px}
.date small{display:block;font-size:12px;line-height:14px}
.card.raised .date{background:var(--orange)}
.card h4{position:absolute;left:78px;top:189px;font-size:15.5px;font-weight:600;line-height:22px}
.card p{position:absolute;left:19px;top:254px;width:240px;font-size:12px;line-height:19px;color:#7a7a7a}
.card .more{position:absolute;left:19px;top:318px;font-size:13px;font-weight:700;color:var(--orange)}

/* contact */
.skyline{left:0;top:3010px;width:1200px;height:226px;background:linear-gradient(180deg,rgba(235,235,235,0) 0%,#efefef 60%,#e6e6e6 100%)}
.field{background:var(--white);border:1.5px solid #a8a8a8;font-size:14px;color:#555;padding:0 20px;display:flex;align-items:center}
.field.area{align-items:flex-start;padding-top:14px}
.submit{left:524px;top:3125px;width:153px;height:43px}

/* footer */
.footer{left:0;top:3236px;width:1200px;height:146px;background:var(--footer)}
.foot-nav{left:144px;top:3277px;font-size:16px;font-weight:700;color:var(--white);letter-spacing:.3px;word-spacing:2px}
.foot-nav span{margin:0 14px;font-weight:400}
.copy{left:700px;top:3280px;font-size:12.5px;color:var(--white)}
.social{top:3326px;width:26px;height:26px;border-radius:50%}
</style>
</head>
<body>

<header>
  <div class="abs brand">Velrato</div>
  <nav class="abs nav">
    <a class="active" style="left:0">Home</a>
    <a style="left:76px">About</a>
    <a style="left:154px">Features</a>
    <a style="left:254px">News</a>
    <a style="left:327px">Contact</a>
  </nav>
  <a class="abs btn btn-orange login">LOGIN</a>
</header>

<section>
  <div class="abs hero-media" role="img" aria-label="Illustration of an office worker at a laptop surrounded by calendar, mail and chat notifications"></div>
  <svg class="abs play" viewBox="0 0 80 80" aria-hidden="true"><circle cx="40" cy="40" r="40" fill="#e43c2f"/><path d="M31 24 L58 40 L31 56 Z" fill="#fff"/></svg>
  <svg class="abs" style="left:43px;top:676px" width="1112" height="520" viewBox="0 0 1112 520" aria-hidden="true">
    <path d="M0 0 H1112 A556 519 0 0 1 0 0 Z" fill="#fc5108"/>
  </svg>
  <h1 class="abs hero-title">Welcome to Velrato</h1>
  <p class="abs hero-copy">Lorem ipsum dolor sit amet, consectetur adipiscing elit, sed do eiusmod tempor incididunt ut labore et dolore magna aliquauis ipsum suspendisse ultrices gravidcommodo viverra maecenas accumsan lacus vel facilisisem ipsum dolor sionsectetur adipiscing ed do eiusmod tempor incididunt ut labore et dolore magna aliquauis ipsum suspendisse ultrices gravidcommodo viverra maecenas accumsan lacus vel facilisis.</p>
  <a class="abs btn btn-blue hero-more">READ MORE</a>
</section>

<section>
  <h2 class="abs section-title" style="top:1312px">Our Features</h2>

  <div class="abs feature" style="left:123px;top:1448px">
    <div class="feature-icon" role="img" aria-label="Step one graphic with a computer screen icon" style="background:linear-gradient(135deg,#f7a21b,#ef6a1e 60%,#e0336e)"></div>
    <h3>Adipisci velit</h3>
    <p>Lorem ipsum dolor sit amonsectetur adipiscing elit, sed do eiusmod tempor incididunt ut labore et dolore magna aliqis ipsum suspendisse ultrices</p>
    <a class="btn btn-blue">GET STARTED</a>
  </div>

  <div class="abs feature" style="left:449px;top:1448px">
    <div class="feature-icon" role="img" aria-label="Step two graphic with a document icon" style="background:linear-gradient(135deg,#d9285f,#8a3fb0 45%,#1fa3d8)"></div>
    <h3>Numquameiue</h3>
    <p>Lorem ipsum dolor sit amonsectetur adipiscing elit, sed do eiusmod tempor incididunt ut labore et dolore magna aliqis ipsum suspendisse ultrices</p>
    <a class="btn btn-blue">GET STARTED</a>
  </div>

  <div class="abs feature" style="left:777px;top:1448px">
    <div class="feature-icon" role="img" aria-label="Step three graphic with a team icon" style="background:linear-gradient(135deg,#1fb6e0,#3a3f9a 60%)"></div>
    <h3>Neque porro</h3>
    <p>Lorem ipsum dolor sit amonsectetur adipiscing elit, sed do eiusmod tempor incididunt ut labore et dolore magna aliqis ipsum suspendisse ultrices</p>
    <a class="btn btn-blue">GET STARTED</a>
  </div>
</section>

<section>
  <div class="abs peach"></div>
  <h2 class="abs section-title" style="top:2086px">Our Features</h2>

  <article class="abs card" style="left:156px;top:2211px">
    <div class="card-art" role="img" aria-label="Illustration of a team reviewing a rules checklist"></div>
    <div class="date">02<small>MAR</small></div>
    <h4>Pellentesque faucibus<br>Ut accumsan ultric</h4>
    <p>Duis quam Nam eget lacus Aliquam erat volutpat Quisque dignissim congue leovel lacus vitae felis vestibulum</p>
    <a class="more">READ MORE</a>
  </article>

  <article class="abs card raised" style="left:462px;top:2211px">
    <div class="card-art" role="img" aria-label="Illustration of recruiters reviewing candidate profiles"></div>
    <div class="date">02<small>MAR</small></div>
    <h4>Pellentesque faucibus<br>Ut accumsan ultric</h4>
    <p>Duis quam Nam eget lacus Aliquam erat volutpat Quisque dignissim congue leovel lacus vitae felis vestibulum</p>
    <a class="more">READ MORE</a>
  </article>

  <article class="abs card" style="left:768px;top:2211px">
    <div class="card-art" role="img" aria-label="Illustration of an employee rating and search workspace"></div>
    <div class="date">02<small>MAR</small></div>
    <h4>Pellentesque faucibus<br>Ut accumsan ultric</h4>
    <p>Duis quam Nam eget lacus Aliquam erat volutpat Quisque dignissim congue leovel lacus vitae felis vestibulum</p>
    <a class="more">READ MORE</a>
  </article>
</section>

<section>
  <div class="abs skyline" role="img" aria-label="Faint line drawing of a city skyline"></div>
  <h2 class="abs section-title" style="top:2822px">Get In Touch</h2>
  <div class="abs field" style="left:172px;top:2942px;width:276px;height:42px">Enter Name</div>
  <div class="abs field" style="left:462px;top:2942px;width:276px;height:42px">Enter Email</div>
  <div class="abs field" style="left:751px;top:2942px;width:276px;height:42px">Enter Phone</div>
  <div class="abs field area" style="left:172px;top:3000px;width:855px;height:96px">Message</div>
  <a class="abs btn btn-blue submit">SUBMIT</a>
</section>

<footer>
  <div class="abs footer"></div>
  <nav class="abs foot-nav">HOME<span>/</span>ABOUT<span>/</span>FEATURES<span>/</span>NEWS<span>/</span>CONTACT</nav>
  <div class="abs copy">© 2022 Velrato. All rights reserved | &nbsp;Privacy | &nbsp;Terms of Use</div>
  <div class="abs social" style="left:146px;background:#3b5bdb"></div>
  <div class="abs social" style="left:180px;background:#1fb3e8"></div>
  <div class="abs social" style="left:214px;background:#2453a6"></div>
</footer>

</body>
</html>
```